Schlichtes Design für Malerbetrieb
Zielgruppe
Wir sind ein mittelgroßer Malerbetrieb in München mit umfangreichem Leistungsspektrum.
Unsere Hauptleistungen sind: Fassadenrenovierung, Altbausanierung, Betoninstandsetzung, Balkonabdichtung (kein Neubau!).
Unsere Zielgruppen sind: Hausverwaltungen, Firmen und Privatpersonen.
Unsere Kunden schätzen: Konstruktive Organisation und Planung im Vorfeld, Zuverlässigkeit, saubere Arbeitsweise, dauerhafte Balkonabdichtungen.
Aufgabenstellung
Wir möchten eine langlebige, stilvolle, minimalistische Homepage.
Wir möchten von der bestehenden Homepage nur die Schriftart für unseren Firmennamen (Century Gothic) und wenn möglich (nicht zwingend), irgendwo das florale Muster einbauen. Corporate-Design haben wir nicht.
Farbtöne: Firmennamen Orange (hellorange bis erdiges Orange möglich, da sind wir nicht fixiert) , einen dunklen Hintergrundfarbton (Petrol-Blaugrau ?) mit gelbem (neon bis senfgelb) Akzent (Linien), Blumenmuster weiß, grau.
Dies sind nur unsere Ideen. Wir sind aber auch absolut offen für eure Profi-Ideen.
Wir möchten uns von den unzähligen langweiligen 'Pinselseiten mit veralteten Bilder' unserer Kollegen interessant und mit Stil abheben.
Eher nach dem Motto 'weniger ist mehr'.
Einen positiven, sympathischen Eindruck geben und unsere Leistungen in den Vordergrund bringen.
Da wir viele Stammkunden haben, betreiben wir kein Social-Media und möchten dies vorerst auch nicht tun.
Die Seite wird in den nächsten Jahren nicht verändert, höchstens die Bilder aktualisiert.
Die Texte haben wir alle selbst entworfen und möchten wir so übernehmen.
Die Galerien sollen unkompliziert anzuschauen sein.
Uns gefällt die Struktur und Schlichtheit von https://vaartmolen.nl/ oder Timbra.de gut und wir mögen Vintage-Grafiken gerne.
Einerseits darf die Seite geradlinig, andererseits aber auch rund und floral wirken.

```html
<!DOCTYPE html>
<html lang="de">
<head>
<meta charset="utf-8">
<title>kolbrit – Leistungen</title>
<link href="https://fonts.googleapis.com/css2?family=Catamaran:wght@500;700;800&family=Questrial&family=Open+Sans:wght@400;600&display=swap" rel="stylesheet">
<style>
:root{
  --orange:#f5a623;
  --header:#6b6665;
  --dark:#645c5c;
  --blush:#ece2e2;
  --text:#7d7878;
  --heading:#56504f;
  --white:#ffffff;
  --line:#cfcaca;
}
*{margin:0;padding:0;box-sizing:border-box}
html,body{width:1200px;height:3913px;overflow:hidden}
body{position:relative;background:var(--white);font-family:"Questrial",sans-serif;color:var(--text)}
.abs{position:absolute}

/* header */
.site-header{left:0;top:0;width:1200px;height:130px;z-index:5}
.site-header svg{position:absolute;left:0;top:0}
.brand{position:absolute;left:84px;top:18px;font-family:"Questrial",sans-serif;font-size:54px;color:var(--orange);letter-spacing:1px}
.nav{position:absolute;top:28px;left:0;width:1200px;font-family:"Open Sans",sans-serif;font-size:12px;letter-spacing:.6px;color:#eee}
.nav span{position:absolute}
.nav .active{color:var(--orange);font-weight:600}

/* hero */
.hero{left:0;top:0;width:1200px;height:555px;background:linear-gradient(120deg,#c9d3dc 0%,#b9c6d1 45%,#9fb0be 80%,#a9b7c2 100%)}
.hero-kicker{left:0;width:1175px;top:225px;text-align:center;font-family:"Questrial",sans-serif;font-size:30px;letter-spacing:3px;color:var(--white)}
.hero-title{left:0;width:1175px;top:268px;text-align:center;font-family:"Catamaran",sans-serif;font-weight:800;font-size:52px;line-height:56px;letter-spacing:2px;color:var(--white)}
.side-tools{left:1142px;top:147px;width:58px;z-index:6}
.side-tools div{width:58px;height:59px;background:#8a8585;margin-bottom:3px;display:flex;align-items:center;justify-content:center}

/* service bands */
.band{left:0;width:1200px}
.band-title{left:0;width:1200px;text-align:center;font-family:"Catamaran",sans-serif;font-weight:800;font-size:40px;letter-spacing:2px;color:var(--white);z-index:3}
.card{background:var(--white);box-shadow:0 4px 18px rgba(0,0,0,.12);z-index:2}
.card .col{position:absolute;font-size:13px;line-height:26px;color:var(--text)}
.card .rule{position:absolute;width:1px;background:var(--line)}
.more{font-family:"Open Sans",sans-serif;font-style:italic;font-weight:600;font-size:12px;color:#555;display:inline-flex;align-items:center;gap:4px;margin-top:14px}
.more.back{color:var(--orange)}

/* closing */
.note{left:0;top:2746px;width:1200px;height:590px;background:var(--blush)}
.note-title{left:0;width:1200px;top:2900px;text-align:center;font-family:"Catamaran",sans-serif;font-weight:800;font-size:42px;line-height:54px;letter-spacing:2px;color:var(--heading)}
.footer-bg{left:0;top:3336px;width:1200px;height:577px;background:var(--dark)}
.contact{left:163px;top:3160px;width:873px;height:546px;background:var(--white);z-index:2}
.contact h2{position:absolute;left:27px;top:38px;font-family:"Questrial",sans-serif;font-weight:400;font-size:40px;color:var(--orange);letter-spacing:1px}
.field-label{position:absolute;left:32px;font-size:10px;color:#aaa}
.field{position:absolute;left:32px;width:440px;border:1px solid #e6e2e2}
.divider{position:absolute;left:507px;top:38px;width:1px;height:440px;background:#e3dfdf}
.info{position:absolute;left:534px;top:40px;width:320px;font-family:"Open Sans",sans-serif;font-size:11px;color:#444}
.info .brand-small{font-family:"Questrial",sans-serif;font-size:50px;color:var(--orange);line-height:56px;margin-bottom:14px}
.info .muted{color:#b0aaaa;font-size:10.5px;line-height:28px}
.info p{line-height:28px}
.legal{left:161px;top:3823px;font-size:12px;line-height:20px;color:#d6d0d0}
.links{top:3806px;font-size:12px;line-height:21px;color:#d6d0d0}
</style>
</head>
<body>

<div class="abs hero" role="img" aria-label="Foto: Maler streicht eine Wand mit Rolle und Farbwanne"></div>
<div class="abs hero-kicker">SERVICES</div>
<div class="abs hero-title">UNSERE LEISTUNGEN<br>IM ÜBERBLICK</div>

<header class="abs site-header">
  <svg width="1200" height="130" viewBox="0 0 1200 130">
    <path d="M0 0H1200V72C1000 72 760 50 560 62C380 74 220 112 0 118Z" fill="var(--header)"/>
  </svg>
  <div class="brand">kolbrit</div>
  <nav class="nav">
    <span style="left:598px">HOME</span>
    <span style="left:671px">ÜBER UNS</span>
    <span class="active" style="left:765px">SERVICES</span>
    <span style="left:855px">AUSBILDUNG</span>
    <span style="left:971px">REFERENZEN</span>
    <span style="left:1078px">KONTAKT</span>
  </nav>
</header>

<div class="abs side-tools">
  <div><svg width="30" height="20" viewBox="0 0 30 20" fill="none" stroke="var(--orange)" stroke-width="1.5"><rect x="1" y="1" width="28" height="18"/><path d="M1 1l14 11L29 1"/></svg></div>
  <div><svg width="28" height="28" viewBox="0 0 24 24" fill="none" stroke="var(--orange)" stroke-width="1.4"><path d="M5 3h4l2 5-2.5 1.5a11 11 0 0 0 6 6L16 13l5 2v4a2 2 0 0 1-2 2A17 17 0 0 1 3 5a2 2 0 0 1 2-2z"/></svg></div>
  <div><svg width="28" height="28" viewBox="0 0 24 24" fill="none" stroke="var(--orange)" stroke-width="1.6"><circle cx="10" cy="10" r="6"/><path d="M14.5 14.5L21 21"/></svg></div>
</div>

<!-- Balkonabdichtung -->
<div class="abs band" style="top:555px;height:478px;background:linear-gradient(100deg,#d7a36b,#e6c39a 55%,#d9b48f)" role="img" aria-label="Foto: Balkon mit Blumenkästen und Geländer"></div>
<div class="abs band-title" style="top:522px">BALKONABDICHTUNG</div>
<div class="abs card" style="left:0;top:609px;width:912px;height:315px">
  <div class="rule" style="left:118px;top:50px;height:230px"></div>
  <div class="col" style="left:152px;top:30px;width:350px">Balkone sind sämtlichen Witterungseinflüssen ausgesetzt. Ohne einen umfangreichen, dauerhaften Schutz sind Schäden vorprogrammiert. Erste optische Hinweise auf undichte Balkonböden sind Farbabplatzungen an Balkondecken. Undichte Balkonböden führen im fortgesetzten Stadium zur Schädigung der tragenden Stahleinlagen. Bei nicht rechtzeitig eingeleiteten Instandsetzungsarbeiten führt dies bis zum Verlust der Standsicherheit. Dies bildet letztendlich eine immense Gefahr für die Bewohner und das Gebäude. Mit uns</div>
  <div class="col" style="left:527px;top:30px;width:368px">kommt es nicht so weit. Eindringende Feuchtigkeit auf horizontalen Balkonflächen kann nur durch ein Abdichtungssystem verhindert werden, das keine Schwachstellen offen lässt. Das setzt voraus, dass die Abdichtung fugenlos aufgebracht wird. Auch sämtliche Anschlüsse an Türen und Geländerpfosten müssen in einem Guss in das vollflächige System eingebunden werden. …<br><span class="more">Weiterlesen <svg width="18" height="10" viewBox="0 0 18 10" fill="none" stroke="#555"><path d="M1 1l8 8 8-8"/></svg></span></div>
</div>

<!-- Balkoninstandsetzung -->
<div class="abs band" style="top:1033px;height:759px;background:linear-gradient(110deg,#5d5856,#8a837e 50%,#6e6865)" role="img" aria-label="Foto: Hand im Arbeitshandschuh bei der Betoninstandsetzung"></div>
<div class="abs band-title" style="top:1002px">BALKONINSTANDSETZUNG</div>
<div class="abs card" style="left:319px;top:1097px;width:881px;height:566px">
  <div class="rule" style="left:47px;top:50px;height:210px"></div>
  <div class="col" style="left:71px;top:40px;width:360px">Betonelemente bilden das Skelett eines Gebäudes. Nur durch genügend Schutz können sie die Aufgaben von Tragfähigkeit und Stabilität langfristig erfüllen. Sanierungs- und Schutzmaßnahmen unterliegen in ihrer Art den örtlichen Gegebenheiten und den gewünschten Wirkungen einer fachmännischen Analyse und Planung. Wir erfüllen die hohen Voraussetzungen, welche eine dauerhafte Betoninstandsetzung an den Ausführenden stellt.<br><br>Neuer Beton schützt die notwendigen Armierungseisen durch seine natürliche Stoffalkalität selbst. Diese Alkalität wird jedoch durch die Faktoren Alter, Nutzung und geografische Lagen mit ihren jeweiligen Umwelteinflüssen unterschiedlich rasch neutralisiert. Neutraler Beton verliert die Schutzfunktion.</div>
  <div class="col" style="left:454px;top:40px;width:364px">Diese Alkalität wird jedoch durch die Faktoren Alter, Nutzung und geografische Lagen mit ihren jeweiligen Umwelteinflüssen unterschiedlich rasch neutralisiert. Neutraler Beton verliert die Schutzfunktion. Dies führt dazu, dass die Armierung rostet. Rostende Armierungseisen lassen Bauwerke nach längerer Zeit instabil werden und bilden folglich eine große Gefahr für den Objekterhalt.<br><br>Bei rechtzeitig eingeleiteten Instandsetzungsarbeiten wird die Korrosion gestoppt, die Alkalität wieder hergestellt und mit einem abschließenden luftdichten Anstrichsystem dauerhaft erhalten. Unsere Geräte, Maschinen und Anstrichmittel bewegen sich stets parallel zum Stand der Technik. Das nötige Fachwissen hingegen basiert auf jahrzehntelanger Erfahrung. Wir haben Sie und geben Sie Ihnen gerne weiter.<br><span class="more back">Zurück <svg width="18" height="10" viewBox="0 0 18 10" fill="none" stroke="var(--orange)"><path d="M1 9l8-8 8 8"/></svg></span></div>
</div>

<!-- Farbgestaltung -->
<div class="abs band" style="top:1792px;height:491px;background:linear-gradient(100deg,#f4c07c,#f7cf95 45%,#f3b060 80%,#ea9a45)" role="img" aria-label="Foto: Hand mit aufgefächerter Farbtonkarte"></div>
<div class="abs band-title" style="top:1762px">FARBGESTALTUNG</div>
<div class="abs card" style="left:0;top:1861px;width:908px;height:311px">
  <div class="rule" style="left:118px;top:50px;height:200px"></div>
  <div class="col" style="left:149px;top:30px;width:364px">Farbe an der richtigen Stelle kann belebend und stilvoll wirken. An falscher Stelle hingegen erdrückend und belastend. Die richtige Wahl von Menge und Intensität unterscheidet uns vom Heimwerker. Wir besitzen das Gefühl für Farbe. Bei der Auswahl von Farbtönen im Innenbereich müssen die vorhandenen Materialien, Einrichtungsgegenstände und Beleuchtungen beachtet werden. Freude an Farbtönen ist nur langlebig, wenn bei der Auswahl die Funktion und die gewünschte Stimmung eines Raumes hinterfragt wird.</div>
  <div class="col" style="left:524px;top:30px;width:370px">Planungen von Farbkonzepten im Außenbereich müssen umfangreicher getroffen werden. Angrenzende farbliche Baukörper, Architektur, Bepflanzungen und Alltagsbewegungen sind Faktoren, die in eine Farbgestaltung von Fassaden mit einbezogen werden müssen. Zwischen Betrachter und Gebäude besteht immer eine Distanz. Der Blickwinkel ist größer und weiter als im Innenbereich. …<br><span class="more">Weiterlesen <svg width="18" height="10" viewBox="0 0 18 10" fill="none" stroke="#555"><path d="M1 1l8 8 8-8"/></svg></span></div>
</div>

<!-- Wärmedämmung -->
<div class="abs band" style="top:2283px;height:463px;background:linear-gradient(100deg,#9fb4c6,#c7d3dc 45%,#aebfcc)" role="img" aria-label="Foto: Neubau-Fassade mit Leiter und Farbeimern"></div>
<div class="abs band-title" style="top:2253px">WÄRMEDÄMMUNG</div>
<div class="abs card" style="left:337px;top:2342px;width:863px;height:316px">
  <div class="rule" style="left:44px;top:50px;height:220px"></div>
  <div class="col" style="left:72px;top:30px;width:360px">Energiekosten steigen. Wohnobjekte, die vor 1995 erstellt wurden, sind nicht oder nur ungenügend gedämmt. Im Inneren des Gebäudes erzeugte Wärme kann nicht voll genutzt werden. Viel schneller kommt das physikalische Prinzip zum Zuge. Wärme sucht den Ausgleich und verbindet sich mit Kälte. Warme Luft wandert somit ungehindert durch ungedämmte Oberflächen und nagt am Geldbeutel der Immobilienbesitzer. Gerne beseitigen wir Ihnen diese nutzlose, finanzielle Belastung. Eine genügende Wärmedämmung</div>
  <div class="col" style="left:448px;top:30px;width:370px">schont nicht nur die Nebenkosten, sondern sorgt auch für ein behaglicheres Wohlbefinden in den Räumen. Gedämmte Wände, Decken und Böden sind und bleiben konstant warm. Warme Oberflächen können mehr Feuchtigkeit aufnehmen als ungedämmte Kalte. Bei richtiger Lüftungsmethode entfällt so die Gefahr von Kondenswasserbildung. …<br><span class="more">Weiterlesen <svg width="18" height="10" viewBox="0 0 18 10" fill="none" stroke="#555"><path d="M1 1l8 8 8-8"/></svg></span></div>
</div>

<!-- closing -->
<div class="abs note"></div>
<div class="abs note-title">HIER ENTSTEHEN SPÄTER NOCH<br>ANDERE LEISTUNGEN IM GLEICHEN DESIGN</div>
<div class="abs footer-bg"></div>

<section class="abs contact">
  <h2>PREISANFRAGE</h2>
  <div class="field-label" style="top:96px">Vor- und Nachname</div>
  <div class="field" style="top:112px;height:40px"></div>
  <div class="field-label" style="top:184px">E-Mail Adresse</div>
  <div class="field" style="top:200px;height:40px"></div>
  <div class="field-label" style="top:268px">Ihre Nachricht</div>
  <div class="field" style="top:284px;height:224px"></div>
  <div class="divider"></div>
  <div class="info">
    <div class="brand-small">kolbrit</div>
    <div class="muted">Als sachkundiger und verantwortungsbewusster Dienstleister für Malerarbeiten und Co stehen wir Ihnen gerne zur Verfügung.</div>
    <p style="margin-top:22px">Haben Sie Fragen oder benötigen weitere Informationen nehmen Sie gerne Kontakt mit uns auf.</p>
    <p style="margin-top:20px;line-height:20px">TELEFON &amp; FAX<br>089 55 01 20 | 089 55 01 31</p>
    <p style="margin-top:26px;line-height:20px">EMAIL<br>info@kolbrit-gmbh.de</p>
    <p style="margin-top:22px;line-height:20px">Werkstatt: Lindenhofstraße 12 | 81371 München<br>Büro: Birkenweg 7 | 82049 Pullach</p>
  </div>
</section>

<div class="abs legal">© 2019 KOLBRIT GmbH. All rights reserved.<br>Birkenweg 7<br>82049 Pullach</div>
<div class="abs links" style="left:893px">Preisanfrage<br>Standorte<br>Service<br>Umfang</div>
<div class="abs links" style="left:992px">Jobs<br>Impressum<br>Datenschutz<br>Rechtliche Hinweise</div>

</body>
</html>
```